BRISKEL Need a luxury modern business card designed.

Need a luxury modern business card designed. refer to the uploaded files for the company name and logo in the zip file under source files. i will making my descion on monday. so please send in before then so if we need to edit we will have the time. we have a trade show coming up and im on a deadline for printer.

Target Market(s)

high end clients

Contact Information for Business Card

Company nAme and logo. Tobias Fennick Co-Founder / Project Manager Office # 555-318-7094 Cell # 555-642-1586 BRISKEL.CA Tobias@briskel-example.ca

Font styles to use
Other font styles liked:
• Modern

Requirements
Must have
• Company name and logo, contact info, using the black, gold and white color scheme.

```html
<!DOCTYPE html>
<html lang="en">
<head>
<meta charset="UTF-8">
<title>BRISKEL — Business Card</title>
<link rel="stylesheet" href="https://fonts.googleapis.com/css2?family=Poppins:wght@300;400;500&display=swap">
<style>
  :root {
    --stage: #1b1b1d;
    --card: #232627;
    --card-edge: #2c2f30;
    --gold: #b8a06a;
    --white: #f2f2f0;
    --silver: #a9abad;
    --muted: #9b9d9e;
  }
  * { margin: 0; padding: 0; box-sizing: border-box; }
  html, body {
    width: 1200px; height: 800px; overflow: hidden;
    background: var(--stage);
    font-family: "Poppins", sans-serif;
  }
  .stage {
    width: 1200px; height: 800px;
    display: flex; align-items: center; justify-content: center; gap: 40px;
  }
  .card {
    position: relative;
    width: 540px; height: 309px;
    background: var(--card);
    border: 1px solid var(--card-edge);
    border-radius: 3px;
  }
  /* Front */
  .card--front { display: flex; align-items: center; justify-content: center; }
  .wordmark {
    display: flex; align-items: center; gap: 14px;
    font-weight: 300; letter-spacing: 0.22em;
  }
  .wordmark__mark { width: 12px; height: 12px; }
  .card--front .wordmark { font-size: 40px; color: var(--silver); }
  .card--front .wordmark__mark { background: var(--silver); }
  /* Back */
  .card--back { display: flex; align-items: center; }
  .card--back .brand {
    width: 250px; display: flex; justify-content: center;
  }
  .card--back .wordmark { font-size: 30px; color: var(--white); }
  .card--back .wordmark__mark { background: var(--gold); width: 10px; height: 10px; }
  .divider {
    width: 1px; height: 150px; background: var(--gold); opacity: 0.8;
  }
  .details { padding-left: 30px; }
  .person__name {
    font-size: 19px; font-weight: 400; letter-spacing: 0.02em;
    color: var(--white); text-transform: uppercase; line-height: 1.1;
  }
  .person__surname { color: var(--gold); }
  .person__role {
    font-size: 10.5px; font-weight: 300; color: var(--muted);
    margin-top: 4px; margin-bottom: 18px;
  }
  .contacts { list-style: none; }
  .contacts li {
    display: flex; align-items: center; gap: 10px;
    font-size: 11px; font-weight: 300; color: var(--white);
    line-height: 1.95;
  }
  .contacts svg { width: 11px; height: 11px; flex: none; }
</style>
</head>
<body>
<main class="stage">
  <section class="card card--front" aria-label="Card front">
    <div class="wordmark"><span class="wordmark__mark"></span><span>BRISKEL</span></div>
  </section>

  <section class="card card--back" aria-label="Card back">
    <div class="brand">
      <div class="wordmark"><span class="wordmark__mark"></span><span>BRISKEL</span></div>
    </div>
    <div class="divider"></div>
    <div class="details">
      <h1 class="person__name">Tobias <span class="person__surname">Fennick</span></h1>
      <p class="person__role">Co-Founder / Project Manager</p>
      <ul class="contacts">
        <li>
          <svg viewBox="0 0 12 12" aria-hidden="true"><path d="M1 4c0-2 2-3 5-3s5 1 5 3l-2 1-1-2H4L3 5 1 4zM3 6h6l1 5H2l1-5z" fill="var(--gold)"/></svg>
          555-318-7094
        </li>
        <li>
          <svg viewBox="0 0 12 12" aria-hidden="true"><rect x="3" y="1" width="6" height="10" rx="1" fill="none" stroke="var(--gold)" stroke-width="1.2"/></svg>
          555-642-1586
        </li>
        <li>
          <svg viewBox="0 0 12 12" aria-hidden="true"><g fill="none" stroke="var(--gold)" stroke-width="1"><circle cx="6" cy="6" r="5"/><ellipse cx="6" cy="6" rx="2.2" ry="5"/><path d="M1 6h10"/></g></svg>
          BRISKEL.CA
        </li>
        <li>
          <svg viewBox="0 0 12 12" aria-hidden="true"><rect x="1" y="2.5" width="10" height="7" fill="var(--gold)"/><path d="M1 2.5l5 4 5-4" fill="none" stroke="var(--card)" stroke-width="1"/></svg>
          Tobias@briskel-example.ca
        </li>
      </ul>
    </div>
  </section>
</main>
</body>
</html>
```